Profesional personal website needs design and business card

I need a business card with my professional name as a logo "Dorian Vitality" for my business. I am a Wellness Coach, consultant and trainer. So it should be professional, wellness oriented and modern.

Target Market(s)

Private clients, governments, corporations. Luxury and high market.

Industry/Entity Type

Health And Wellness

Contact Information for Business Card

Dorian Vitality should be the logo

Colors

Designer to choose colors to be used in the design.

Requirements
Must have
• Dorian Vitality
• Name: Tomás Lirandel
• Wellness Coach, Consultant & Trainer.
• Website: www.dorianvitality-example.com
• Phone:
• Spain (+34) 612 480 317
• (USA) +1 (555) 610 4829
Nice to have
• The most important is the design of "Dorian Vitality", as this is going to be my personal brand logo. It should be professional, wellness, high end and actual.
Should not have
• no golds, no baroque style..

```html
<!DOCTYPE html>
<html lang="en">
<head>
<meta charset="utf-8">
<title>Dorian Vitality – Business Card</title>
<link rel="stylesheet" href="https://fonts.googleapis.com/css2?family=Montserrat:wght@400;500;700&display=swap">
<style>
  :root {
    --navy: #1a2a9c;
    --sun: #f7b90f;
    --ink: #1d1d2b;
    --paper: #ffffff;
    --backdrop: #2b2b2d;
  }
  * { margin: 0; padding: 0; box-sizing: border-box; }
  html, body {
    width: 1200px; height: 930px; overflow: hidden;
    background: var(--backdrop);
    font-family: "Montserrat", sans-serif;
  }
  .canvas { position: relative; width: 1200px; height: 930px; }
  .card {
    position: absolute; width: 640px; height: 366px;
    background: var(--paper); border-radius: 26px; overflow: hidden;
    box-shadow: 0 14px 30px rgba(0,0,0,.45);
  }
  .card--front { left: 60px; top: 50px; }
  .card--back { left: 500px; top: 500px; }

  .brand {
    color: var(--navy); font-weight: 700; text-transform: uppercase;
    line-height: 1; letter-spacing: 1px;
  }
  .card--front .brand {
    position: absolute; left: 0; right: 0; top: 150px;
    text-align: center; font-size: 52px;
  }
  .card--back .brand {
    position: absolute; right: 30px; top: 30px; font-size: 26px; text-align: right;
  }

  .holder { position: absolute; left: 32px; top: 44px; }
  .holder__name {
    font-size: 30px; font-weight: 700; text-transform: uppercase;
    color: var(--navy); letter-spacing: .5px;
  }
  .holder__name .surname { color: var(--sun); }
  .holder__role { font-size: 13px; color: var(--ink); margin-top: 4px; }

  .address {
    position: absolute; right: 42px; top: 150px;
    font-size: 14px; color: var(--ink); text-align: right; line-height: 1.45;
  }

  .contacts { position: absolute; left: 44px; top: 192px; list-style: none; }
  .contacts li {
    display: flex; align-items: center; gap: 10px;
    font-size: 14px; color: var(--ink); height: 22px;
  }
  .contacts svg { width: 14px; height: 14px; flex: none; }
  .contacts .flag { width: 22px; height: 14px; margin-left: 8px; }
  .contacts .accent { color: var(--sun); }

  .wave { position: absolute; left: 0; bottom: 0; width: 640px; height: 366px; }
</style>
</head>
<body>
<main class="canvas">
  <section class="card card--front" aria-label="Card front">
    <p class="brand">Dorian Vitality</p>
  </section>

  <section class="card card--back" aria-label="Card back">
    <svg class="wave" viewBox="0 0 640 366" aria-hidden="true">
      <path d="M0,366 L0,300 C160,262 360,288 640,180 L640,366 Z" fill="var(--sun)"/>
      <path d="M0,366 L0,312 C170,276 370,300 640,196 L640,366 Z" fill="var(--navy)"/>
    </svg>

    <div class="holder">
      <h1 class="holder__name">Tomás <span class="surname">Lirandel</span></h1>
      <p class="holder__role">Wellness Coach, Consultant &amp; Trainer</p>
    </div>

    <p class="brand">Dorian Vitality</p>

    <p class="address">1480 Marlowe Ave<br>Ashbury, BC, V0X 9Z9</p>

    <ul class="contacts">
      <li>
        <svg viewBox="0 0 14 14"><path d="M3 1l2 3-1.3 1.2c.8 1.8 2.3 3.3 4.1 4.1L9 8l3 2-1 2.5C6 12.5 1.5 8 1.5 2.8Z" fill="var(--navy)"/></svg>
        (+34) 612 480 317
        <svg class="flag" viewBox="0 0 22 14" aria-hidden="true"><rect width="22" height="14" fill="#c60b1e"/><rect y="3.5" width="22" height="7" fill="#ffc400"/></svg>
      </li>
      <li>
        <svg viewBox="0 0 14 14"><rect x="3.5" y="1" width="7" height="12" rx="1.3" fill="none" stroke="var(--navy)" stroke-width="1.4"/><circle cx="7" cy="11" r=".8" fill="var(--navy)"/></svg>
        +1 (555) 610 4829
        <svg class="flag" viewBox="0 0 22 14" aria-hidden="true"><rect width="22" height="14" fill="#fff"/><g fill="#b22234"><rect y="0" width="22" height="2"/><rect y="4" width="22" height="2"/><rect y="8" width="22" height="2"/><rect y="12" width="22" height="2"/></g><rect width="9" height="7" fill="#3c3b6e"/></svg>
      </li>
      <li>
        <svg viewBox="0 0 14 14"><rect x="1" y="3" width="12" height="8" fill="none" stroke="var(--navy)" stroke-width="1.4"/><path d="M1 3l6 5 6-5" fill="none" stroke="var(--navy)" stroke-width="1.4"/></svg>
        info@dorianvitality-example.com
      </li>
      <li>
        <svg viewBox="0 0 14 14"><circle cx="7" cy="7" r="5.8" fill="none" stroke="var(--navy)" stroke-width="1.3"/><ellipse cx="7" cy="7" rx="2.4" ry="5.8" fill="none" stroke="var(--navy)" stroke-width="1.1"/><path d="M1.2 7h11.6" stroke="var(--navy)" stroke-width="1.1"/></svg>
        <span>www.<span class="accent">dorianvitality-example</span>.com</span>
      </li>
    </ul>
  </section>
</main>
</body>
</html>
```